Lawn Sign For Construction Projects - Brisk Harbor

This contest is for a lawn sign that will be placed in the front yard of recently completed construction projects. The goal here is to have a bold advertising sign that is visible from a vehicle driving past.

We are still deciding on the default size for our sign, we also may use multiple sizes. The two sizes we will more than likely be using are: 18"h x 24"w and 24"h x 36"w.

Preference will be given to designers that submit original designs that tie into our current brand and are either in both the size formats listed above or are easy to scale in photoshop or illustrator.

In the files, you will see our logo and an example of a lawn sign.

Please contact us with any questions or comments you may have!

Thank You,
- The Brisk Harbor Team
Updates

Project Deadline Extended Reason: We Currently to not have any designs worth choosing. Added Monday, March 21, 2016

Industry/Entity Type

Residential Construction

Colors
34a7d8
ffffff
faa54b

Requirements
Nice to have
• 1. The sign must tie into our current branding and color scheme.
• 2. The sign must be clearly visible and readable.
• 3. The sign must include our phone number in readable print.
• 4. Our website written in small print along the bottom of the sign.
• 5. Must mention we install the following products:
• a.) Solar
• b.) Roofing
• c.) Windows
• d.) Artificial Lawn
• e.) Whole House Fans
• f.) Patio Covers

```html
<!DOCTYPE html>
<html lang="en">
<head>
<meta charset="utf-8">
<title>Brisk Harbor – Lawn Sign</title>
<link href="https://fonts.googleapis.com/css2?family=Archivo+Black&family=Montserrat:wght@400;600;700&family=Oswald:wght@700&display=swap" rel="stylesheet">
<style>
  :root {
    --backdrop: #e6e9e4;
    --white: #ffffff;
    --sky-blue: #34a7d8;
    --deep-blue: #1a74a6;
    --warm-orange: #faa54b;
    --light-orange: #ffd29c;
    --ink: #000000;
  }
  * { margin: 0; padding: 0; box-sizing: border-box; }
  html, body { width: 1200px; height: 1200px; overflow: hidden; }
  body { background: var(--backdrop); position: relative; }

  .lawn-sign {
    position: absolute;
    left: 82px; top: 211px;
    width: 1036px; height: 777px;
    background: radial-gradient(ellipse at 50% 45%, var(--light-orange) 0%, #fdb866 50%, var(--warm-orange) 100%);
    overflow: hidden;
    box-shadow: 0 6px 18px rgba(0,0,0,0.18);
  }
  .header-band { position: absolute; left: 0; top: 0; width: 1036px; height: 195px; }

  .brand {
    position: absolute; top: 62px; left: 0; width: 100%;
    display: flex; align-items: center; justify-content: center; gap: 20px;
  }
  .brand-dot { width: 62px; height: 62px; border-radius: 50%; background: var(--warm-orange); }
  .brand-name {
    font-family: "Montserrat", sans-serif; font-weight: 700;
    font-size: 56px; letter-spacing: -1px; color: var(--deep-blue);
  }

  .headline-top {
    position: absolute; top: 192px; left: 0; width: 100%;
    text-align: center;
    font-family: "Oswald", sans-serif; font-weight: 700;
    font-size: 150px; line-height: 1; color: var(--ink);
    letter-spacing: 7px;
  }
  .headline-main {
    position: absolute; top: 332px; left: 0; width: 100%;
    text-align: center;
    font-family: "Archivo Black", sans-serif;
    font-size: 188px; line-height: 1; color: var(--ink);
    letter-spacing: -3px;
  }
  .product-list {
    position: absolute; top: 522px; left: 0; width: 100%;
    text-align: center;
    font-family: "Montserrat", sans-serif; font-weight: 700;
    font-size: 25px; line-height: 1; color: var(--deep-blue);
    letter-spacing: 0.5px;
  }

  .contact-band {
    position: absolute; left: 0; bottom: 0; width: 100%; height: 200px;
    background: var(--deep-blue); color: var(--white); text-align: center;
    font-family: "Montserrat", sans-serif;
  }
  .phone { font-weight: 400; font-size: 108px; line-height: 1; margin-top: 18px; letter-spacing: 1px; }
  .website { font-weight: 600; font-size: 40px; line-height: 1; margin-top: 14px; letter-spacing: 1px; }
</style>
</head>
<body>
  <div class="lawn-sign">
    <svg class="header-band" viewBox="0 0 1036 195" aria-hidden="true">
      <path d="M0 0 H1036 V117 Q518 262 0 117 Z" fill="var(--white)"/>
    </svg>

    <div class="brand">
      <span class="brand-dot"></span>
      <span class="brand-name">BRISK HARBOR</span>
    </div>

    <div class="headline-top">We've Gone</div>
    <div class="headline-main">Solar</div>
    <div class="product-list">ROOFING · WINDOWS · ARTIFICIAL LAWN · WHOLE HOUSE FANS · PATIO COVERS</div>

    <div class="contact-band">
      <div class="phone">044 555 0192</div>
      <div class="website">www.briskharbor.com</div>
    </div>
  </div>
</body>
</html>
```